food delivery web site design

Currently we have a smartphone app (ios/android) that is being used by our clients to make orders to about 30 different restaurants.

We would like to extent this and have also a website that is able to mimic the same functionalities:
- register
- show restaurants based on the selected address
- make order to an restaurant
- being able to process orders for other registered users (please read the attached doc for complete info on this)

Take a look at the attached doc for more info.

```html
<!DOCTYPE html>
<html lang="ro">
<head>
<meta charset="utf-8">
<title>DishDash – Meniu</title>
<link href="https://fonts.googleapis.com/css2?family=Oswald:wght@300;400;500&family=Open+Sans:ital,wght@0,400;0,600;1,600&display=swap" rel="stylesheet">
<style>
:root{
  --red:#a3170c;
  --red-dark:#8c1209;
  --ink:#2a2a2a;
  --tab:#2b2323;
  --muted:#777;
  --line:#d9d9d9;
  --pale:#f1f1f1;
  --gold:#e9b200;
  --green:#3a9a2a;
  --footer:#2a2a2a;
}
*{box-sizing:border-box;margin:0;padding:0}
html,body{width:1076px;height:1200px;overflow:hidden;background:#fff}
body{position:relative;font-family:"Open Sans",sans-serif;color:var(--ink)}
.abs{position:absolute}
.pattern-band{left:0;top:0;width:1076px;height:45px;background:linear-gradient(#fafafa,#efefef)}
.topbar{left:0;top:45px;width:1076px;height:48px;background:var(--red);border-bottom:2px solid var(--red-dark);display:flex;align-items:center}
.topbar .rule{position:absolute;top:23px;height:1px;background:rgba(255,255,255,.55)}
.call{position:absolute;left:314px;top:8px;font-family:Oswald,sans-serif;font-size:23px;color:#fff;letter-spacing:-.3px;display:flex;align-items:center;gap:6px}
.call .num{color:#f5c23a}
.dots{position:absolute;left:547px;top:23px;width:248px;border-top:2px dotted rgba(255,255,255,.4)}
.auth{position:absolute;top:14px;font-family:Oswald,sans-serif;font-size:14px;color:#fff;display:flex;align-items:center;gap:5px}
.brand-tab{left:124px;top:0;width:141px;height:141px}
.brand-circle{position:absolute;left:21px;top:20px;width:100px;height:100px;border-radius:50%;background:#fff;display:flex;align-items:center;justify-content:center;font-family:Oswald,sans-serif;font-weight:500;font-size:19px;color:var(--red)}
.share{left:711px;top:132px;display:flex;align-items:center;gap:6px;font-size:10px;letter-spacing:.5px;color:#444}
.share .field{width:166px;height:25px;border:1px solid var(--red);font-size:9.5px;padding:5px 6px;white-space:nowrap;overflow:hidden;color:#333;letter-spacing:0}
.hint{left:852px;top:166px;font-size:8.5px;color:#444;display:flex;gap:5px;align-items:center}
.hint i{color:var(--red);font-weight:600;font-family:Georgia,serif;font-size:12px}
.thumb{left:124px;top:205px;width:56px;height:45px;background:linear-gradient(135deg,#8a6d4d,#4a3a2a)}
.rest-name{left:190px;top:199px;font-family:Oswald,sans-serif;font-size:27px;color:var(--red);letter-spacing:-.3px}
.stars{left:191px;top:240px;color:var(--gold);font-size:13px;letter-spacing:4px;display:flex;align-items:center}
.stars a{color:var(--green);font-size:9.5px;font-weight:600;letter-spacing:0;margin-left:6px;text-decoration:underline;font-family:"Open Sans",sans-serif}
.tags{left:405px;top:210px;display:flex;gap:24px;font-family:Oswald,sans-serif;font-size:17px;color:#333}
.tags span{display:flex;align-items:center;gap:4px}
.tags svg{fill:var(--red);stroke:var(--red)}
.menu-word{left:808px;top:188px;font-family:Oswald,sans-serif;font-weight:500;font-size:64px;color:#cdcdcd;letter-spacing:1px}
.hr{left:124px;top:266px;width:828px;height:1px;background:var(--line)}
.vline{left:281px;top:266px;width:1px;height:884px;background:var(--line)}
.sidebar{left:124px;top:266px;width:157px;border-left:1px solid var(--line)}
.sidebar h3{height:32px;background:#1e1e1e;color:#fff;font-family:Oswald,sans-serif;font-weight:400;font-size:15px;padding:6px 11px}
.sidebar li{list-style:none;height:35px;border-bottom:1px solid #e6e6e6;font-family:Oswald,sans-serif;font-size:13.5px;color:#999;padding:8px 11px;letter-spacing:.2px}
.sidebar li.active{color:var(--red);border-left:3px solid var(--red);padding-left:17px;margin-left:-1px}
.section-title{left:314px;font-family:Oswald,sans-serif;font-size:24px;color:var(--red);letter-spacing:.2px}
.double{left:314px;width:428px;height:4px;border-top:1px solid #ccc;border-bottom:1px solid #ccc}
.dishes{left:281px;top:326px;width:461px}
.dish{height:68px;border-bottom:1px dotted #bdbdbd;position:relative;padding:12px 0 0 35px}
.dish .name{font-size:16px;letter-spacing:.3px;color:#222}
.dish .price{font-size:16px;color:var(--muted);letter-spacing:.3px;margin-top:-1px}
.dish .price em{font-size:12.5px;font-weight:600;color:#666}
.qty{position:absolute;right:0;top:26px;width:58px;height:26px;border:1px solid #ddd;border-bottom:2px solid #ccc;display:flex;align-items:center;font-weight:600;background:#fff}
.qty b{width:17px;text-align:center;color:#444;font-size:15px;line-height:1}
.qty span{flex:1;border-left:1px solid #ddd;text-align:center;color:var(--red);font-weight:400;font-size:14px}
.cart{left:795px;top:281px;width:157px;height:119px;background:var(--pale);box-shadow:0 1px 4px rgba(0,0,0,.3)}
.cart .head{display:flex;height:30px;border-bottom:1px solid #ddd}
.cart .head div{flex:1;display:flex;align-items:center;gap:5px;padding-left:8px;font-family:Oswald,sans-serif;font-size:12.5px;color:#333}
.cart .head a{width:53px;background:var(--red);color:#fff;font-family:Oswald,sans-serif;font-size:12.5px;display:flex;align-items:center;justify-content:center}
.cart ul{padding:8px 10px 0 10px}
.cart li{list-style:none;display:flex;justify-content:space-between;font-family:Oswald,sans-serif;font-weight:300;font-size:9.5px;height:25px;align-items:center;color:#222}
.cart li b{font-weight:500;font-size:13px;letter-spacing:5px}
.footer{left:0;top:1150px;width:1076px;height:50px;background:var(--footer);color:#ddd;font-size:11px}
.footer nav{position:absolute;left:124px;top:18px;display:flex}
.footer nav span{padding:0 8px;border-left:1px solid #555}
.footer nav span:first-child{padding-left:0;border:none}
.footer .copy{position:absolute;right:124px;top:18px}
</style>
</head>
<body>
<div class="abs pattern-band" role="img" aria-label="Decorative band of hand-drawn kitchen and food doodles"></div>
<header class="abs topbar">
  <div class="rule" style="left:265px;width:34px"></div>
  <div class="call">SUNĂ-NE LA
    <svg width="14" height="18" viewBox="0 0 14 18"><path d="M3 1l3 3-2 3c1 3 3 5 5 6l2-2 3 3-2 3C7 17 1 10 1 3z" fill="#f5c23a"/></svg>
    <span class="num">0700 123 456</span></div>
  <div class="dots"></div>
  <div class="auth" style="left:811px"><svg width="13" height="11" viewBox="0 0 13 11"><path d="M1 10V6c0-2 2-3 4-3h3V0l5 5-5 5V7H5C3 7 2 8 1 10z" fill="#fff"/></svg>LOGIN</div>
  <div class="auth" style="left:879px"><svg width="14" height="11" viewBox="0 0 14 11"><circle cx="5" cy="3" r="3" fill="#fff"/><path d="M0 11c0-4 2-5 5-5s5 1 5 5z M10 3h4M12 1v4" fill="#fff" stroke="#fff" stroke-width="1.2"/></svg>SIGN IN</div>
  <div class="rule" style="left:954px;width:122px"></div>
</header>
<div class="abs brand-tab">
  <svg width="141" height="141" viewBox="0 0 141 141"><path d="M0 0h141v118l-20 23H20L0 118z" fill="var(--tab)"/><path d="M5 0v116l17 20h97l17-20V0" fill="none" stroke="#5a4c4c" stroke-width="1"/></svg>
  <div class="brand-circle">DishDash</div>
</div>
<div class="abs share">SHARE MENIU:<div class="field">http://www.dishdash.example/meniu</div></div>
<div class="abs hint"><i>i</i>La ce imi foloseste ?</div>

<div class="abs thumb" role="img" aria-label="Restaurant photo thumbnail"></div>
<h1 class="abs rest-name">LA HANUL VECHI</h1>
<div class="abs stars">★★★★★<a>35 DE REVIEW-URI</a></div>
<div class="abs tags">
  <span><svg width="18" height="18" viewBox="0 0 18 18"><path d="M2 2l14 14M2 2l5 1 1 5" stroke-width="2" fill="none"/></svg>ROMANESC</span>
  <span><svg width="16" height="20" viewBox="0 0 16 20"><path d="M7 0h2v20H7zM1 4h13l2 2-2 2H1zM2 10h12v4H2z" stroke="none"/></svg>3KM</span>
  <span><svg width="20" height="14" viewBox="0 0 20 14"><path d="M0 2h10v2H0zM0 6h10v2H0zM0 10h10v2H0zM12 4h8v2h-8zM12 8h8v2h-8z" stroke="none"/></svg>&lt; 25RON</span>
  <span><svg width="18" height="18" viewBox="0 0 18 18"><circle cx="9" cy="9" r="7.5" fill="none" stroke-width="1.8"/><path d="M9 4v5h4" fill="none" stroke-width="1.8"/></svg>25MIN</span>
</div>
<div class="abs menu-word">MENIU</div>
<div class="abs hr"></div>
<div class="abs vline"></div>

<aside class="abs sidebar">
  <h3>CATEGORII</h3>
  <ul>
    <li class="active">GUSTĂRI (11)</li><li>CIORBE (9)</li><li>PEŞTE (5)</li><li>PREGĂTITE ÎN CASĂ (12)</li><li>GRĂTAR (5)</li><li>GARNITURI (6)</li><li>SALATE (4)</li><li>DESERT (6)</li><li>BĂUTURI (10)</li>
  </ul>
</aside>

<h2 class="abs section-title" style="top:278px">GUSTĂRI</h2>
<div class="abs double" style="top:319px"></div>

<div class="abs dishes">
  <div class="dish"><div class="name">Zacuscă de vinete</div><div class="price">11.00 RON</div><div class="qty"><b>+</b><b>-</b><span>3</span></div></div>
  <div class="dish"><div class="name">Salată de icre de crap</div><div class="price">16.00 RON</div><div class="qty"><b>+</b><b>-</b><span>0</span></div></div>
  <div class="dish"><div class="name">Salata de icre de ştiucă</div><div class="price">22.00 RON</div><div class="qty"><b>+</b><b>-</b><span>0</span></div></div>
  <div class="dish"><div class="name">Fasole bătută</div><div class="price">11.00 RON</div><div class="qty"><b>+</b><b>-</b><span>3</span></div></div>
  <div class="dish"><div class="name">Salată Isaccea</div><div class="price">19.00 RON</div><div class="qty"><b>+</b><b>-</b><span>0</span></div></div>
  <div class="dish"><div class="name">Colţunaşi cu mânătărci</div><div class="price">23.00 RON</div><div class="qty"><b>+</b><b>-</b><span>0</span></div></div>
  <div class="dish"><div class="name">Jumări Româneşti</div><div class="price">7.00 RON <em>(100gr/por)</em></div><div class="qty"><b>+</b><b>-</b><span>0</span></div></div>
  <div class="dish"><div class="name">Tobă Ţărănească</div><div class="price">7.00 RON <em>(100gr/por)</em></div><div class="qty"><b>+</b><b>-</b><span>0</span></div></div>
  <div class="dish"><div class="name">Slănină Afumată</div><div class="price">3.00 RON <em>(50gr/por)</em></div><div class="qty"><b>+</b><b>-</b><span>0</span></div></div>
  <div class="dish"><div class="name">Şorici</div><div class="price">9.00 RON <em>(50gr/por)</em></div><div class="qty"><b>+</b><b>-</b><span>0</span></div></div>
  <div class="dish"><div class="name">Caltaboş</div><div class="price">7.00 RON <em>(100gr/por)</em></div><div class="qty"><b>+</b><b>-</b><span>0</span></div></div>
</div>

<h2 class="abs section-title" style="top:1090px">CIORBE</h2>
<div class="abs double" style="top:1130px"></div>

<aside class="abs cart">
  <div class="head"><div><svg width="14" height="12" viewBox="0 0 14 12"><path d="M0 1h3l2 7h7l2-5H4" fill="none" stroke="#333" stroke-width="1.3"/><circle cx="6" cy="10.5" r="1.2" fill="#333"/><circle cx="11" cy="10.5" r="1.2" fill="#333"/></svg>COŞUL MEU</div><a>DETALII</a></div>
  <ul>
    <li>ZACUSCĂ DE VINETE (3)<b>+-</b></li>
    <li>FASOLE BĂTUTĂ (3)<b>+-</b></li>
    <li>"TACI ŞI-NGHITE!" (1)<b>+-</b></li>
  </ul>
</aside>

<footer class="abs footer" role="img" aria-label="Dark footer band with faint food doodle pattern">
  <nav><span>Contactează-ne</span><span>Despre noi</span><span>Partenerii noştri</span><span>FAQ</span><span>Devino partener</span></nav>
  <div class="copy">Copyright © 2013 DishDash.example. Toate drepturile rezervate.</div>
</footer>
</body>
</html>
```